Business Card Design

We are a commercial real estate brokerage in San Francisco, leasing office buildings downtown.
I would like a clean, elegant look. Simple but powerful .

Industry/Entity Type

Business

Contact Information for Business Card

Derek Holloway
lic# 07258143
415.555.0172
derek@velt-commercial.example
velt-commercial.example

```html
<!DOCTYPE html>
<html lang="en">
<head>
<meta charset="utf-8">
<title>VELT Commercial — Business Card</title>
<link rel="stylesheet" href="https://fonts.googleapis.com/css2?family=Source+Sans+3:wght@400;600&display=swap">
<style>
  :root {
    --bg: #e9e7e3;
    --card: #ffffff;
    --ink-dark: #3b3b3d;
    --slate: #7d8aa6;
    --text-grey: #555759;
    --rule: #b9bcc2;
    --sky-light: #c9cbcf;
    --sky-dark: #55575b;
  }
  * { box-sizing: border-box; margin: 0; padding: 0; }
  html, body { width: 1200px; height: 950px; overflow: hidden; }
  body {
    background: var(--bg);
    font-family: "Source Sans 3", "Myriad Pro", sans-serif;
    position: relative;
  }
  .card {
    position: absolute;
    width: 620px;
    height: 354px;
    background: var(--card);
    box-shadow: 0 10px 28px rgba(0,0,0,0.18);
    overflow: hidden;
  }
  .card-back { left: 70px; top: 80px; }
  .card-front { left: 510px; top: 510px; }
  .card-shapes { position: absolute; inset: 0; width: 100%; height: 100%; }

  .skyline {
    position: absolute;
    background: linear-gradient(180deg, var(--sky-light) 0%, #8e9095 55%, var(--sky-dark) 100%);
  }
  .card-back .skyline { left: 190px; top: 55px; width: 240px; height: 160px; }

  .tagline {
    position: absolute;
    right: 28px; top: 243px;
    color: #ffffff;
    font-size: 15px;
    line-height: 1.3;
    text-align: right;
  }

  .brand {
    position: absolute;
    left: 232px; top: 62px;
    display: flex; align-items: center; gap: 14px;
  }
  .brand .skyline { position: static; width: 84px; height: 62px; }
  .brand-divider { width: 1px; height: 78px; background: var(--rule); }
  .brand-name {
    color: var(--slate);
    font-weight: 400;
    line-height: 0.95;
  }
  .brand-name .word-main { display: block; font-size: 46px; letter-spacing: 1px; }
  .brand-name .word-sub { display: block; font-size: 20px; letter-spacing: 3px; }

  .license {
    position: absolute;
    right: 26px; top: 186px;
    color: var(--text-grey);
    font-size: 14px;
  }
  .website {
    position: absolute;
    right: 22px; top: 261px;
    color: #ffffff;
    font-size: 15px;
    line-height: 20px;
    white-space: nowrap;
  }
  .holder {
    position: absolute;
    left: 40px; top: 200px;
    width: 300px;
  }
  .holder-name {
    color: var(--slate);
    font-size: 22px;
    font-weight: 400;
    letter-spacing: 1px;
    text-transform: uppercase;
    padding-bottom: 6px;
    border-bottom: 1px solid var(--rule);
  }
  .contact-list { list-style: none; margin-top: 8px; }
  .contact-list li {
    display: flex; align-items: center; gap: 10px;
    color: var(--text-grey);
    font-size: 14px;
    line-height: 22px;
  }
  .contact-list svg { width: 13px; height: 13px; fill: var(--slate); flex: none; }
</style>
</head>
<body>

<section class="card card-back" aria-label="Card back">
  <svg class="card-shapes" viewBox="0 0 620 354" preserveAspectRatio="none" aria-hidden="true">
    <polygon points="278,228 620,228 620,302 262,302" fill="var(--ink-dark)"/>
    <polygon points="0,318 258,300 246,354 0,354" fill="var(--slate)"/>
  </svg>
  <div class="skyline" role="img" aria-label="Illustration of downtown office towers"></div>
  <p class="tagline">commercial real estate brokerage in San Francisco<br>leasing office buildings downtown.</p>
</section>

<section class="card card-front" aria-label="Card front">
  <svg class="card-shapes" viewBox="0 0 620 354" preserveAspectRatio="none" aria-hidden="true">
    <line x1="120" y1="172" x2="620" y2="172" stroke="var(--rule)" stroke-width="1"/>
    <polygon points="382,248 620,248 620,296 366,296" fill="var(--ink-dark)"/>
    <polygon points="0,342 364,300 620,300 620,316 0,354" fill="var(--slate)"/>
  </svg>

  <div class="brand">
    <div class="skyline" role="img" aria-label="Small illustration of office towers"></div>
    <span class="brand-divider"></span>
    <p class="brand-name"><span class="word-main">VELT</span><span class="word-sub">COMMERCIAL</span></p>
  </div>

  <p class="license">lic# 07258143</p>
  <p class="website">www.velt-commercial.example</p>

  <div class="holder">
    <h1 class="holder-name">Derek Holloway</h1>
    <ul class="contact-list">
      <li>
        <svg viewBox="0 0 24 24" aria-hidden="true"><path d="M6.6 10.8a15.1 15.1 0 0 0 6.6 6.6l2.2-2.2a1 1 0 0 1 1-.25 11.4 11.4 0 0 0 3.6.57 1 1 0 0 1 1 1V20a1 1 0 0 1-1 1A17 17 0 0 1 3 4a1 1 0 0 1 1-1h3.5a1 1 0 0 1 1 1c0 1.25.2 2.45.57 3.57a1 1 0 0 1-.25 1z"/></svg>
        415.555.0172
      </li>
      <li>
        <svg viewBox="0 0 24 24" aria-hidden="true"><path d="M2 5h20v14H2z M3.5 6.5 12 13l8.5-6.5" fill="var(--slate)" stroke="#fff" stroke-width="1.4"/></svg>
        derek@velt-commercial.example
      </li>
    </ul>
  </div>
</section>

</body>
</html>
```